Summit Builders Web Site / Business Cards

Construction Company that specializes in Water and Fire Damage, Residential ReModels, Landscaping and Building ADU (Accessory Dwelling Unit)

Growing and changing families often need additional space, and a remodeling project can often provide that. Adding a new area, or repurposing an existing one can satisfy this requirement.

Other times, homeowners want to update the look in their kitchen or bathroom with more than just a change of cabinetry or vanity doors and drawers. Whatever your needs are, Summit Builders has skilled workers who are bonded and insured, and ready to make your dreams and visions a reality.

Target Market(s)

Home Owners

Industry/Entity Type

Construction Company

Contact Information for Business Card

Center Logo with our information on the corners

Back side to be Logo Only
Contact Info
CSLB License # 2418596
info@summitbuildersca.example
www.summitbuildersca.example

Coding

Coded - Design and coding required

Number of Pages Required

5+ page

Font styles to use
Serif
Sans Serif

Requirements
Must have
• Using our Logo Colors
Home
About Us
Services
Projects / Portfolio
Contact Us
Nice to have
• Colors matching our Logo
Should not have
• Black because it doesnt match our logo

```html
<!DOCTYPE html>
<html lang="en">
<head>
<meta charset="utf-8">
<title>Summit Builders – Business Cards</title>
<link href="https://fonts.googleapis.com/css2?family=Roboto:wght@400;500;700&display=swap" rel="stylesheet">
<style>
  :root {
    --orange: #ff6600;
    --ink: #111111;
    --charcoal: #231c18;
    --paper: #ffffff;
    --canvas: #d8d8d8;
    --text-grey: #333333;
  }
  * { box-sizing: border-box; margin: 0; padding: 0; }
  html, body { width: 1200px; height: 745px; overflow: hidden; background: var(--canvas); }
  body { position: relative; font-family: "Roboto", Arial, sans-serif; }

  .card { position: absolute; width: 520px; height: 297px; overflow: hidden; background: var(--orange); }
  .card--front-top { left: 67px; top: 60px; }
  .card--front-bottom { left: 67px; top: 387px; }
  .card--back-light { left: 613px; top: 60px; background: var(--paper); }
  .card--back-dark { left: 613px; top: 387px; background: var(--charcoal); }

  .card__shape { position: absolute; inset: 0; width: 520px; height: 297px; }

  .skyline {
    position: absolute; left: 0; right: 0; bottom: 0; height: 80px;
    background: linear-gradient(to top, rgba(255,255,255,0.10), rgba(255,255,255,0));
  }
  .card--back-light .skyline { background: linear-gradient(to top, rgba(200,200,200,0.25), rgba(200,200,200,0)); }

  .brand {
    position: absolute; display: flex; flex-direction: column; align-items: center; text-align: center;
    color: var(--ink);
  }
  .brand__mark { width: 30px; height: 30px; background: var(--ink); margin-bottom: 14px; }
  .brand__name { font-weight: 700; text-transform: uppercase; letter-spacing: 2px; line-height: 1; }
  .brand__license { font-weight: 500; font-size: 13px; margin-top: 26px; }

  .card--front-top .brand { left: 0; right: 0; top: 66px; }
  .card--front-top .brand__name { font-size: 32px; }
  .card--front-bottom .brand { left: 0; right: 0; top: 88px; }
  .card--front-bottom .brand__name { font-size: 36px; }
  .card--front-bottom .brand__license { margin-top: 40px; }

  .card--back-light .brand, .card--back-dark .brand { left: 20px; width: 196px; top: 62px; }
  .card--back-light .brand__name, .card--back-dark .brand__name { font-size: 21px; letter-spacing: 1px; }

  .person { position: absolute; left: 286px; top: 38px; }
  .person__name { font-weight: 700; font-size: 25px; line-height: 1; }
  .person__title { font-size: 17px; margin-top: 10px; }
  .card--back-light .person__name { color: var(--ink); }
  .card--back-light .person__title { color: var(--text-grey); }
  .card--back-dark .person__name, .card--back-dark .person__title { color: var(--paper); }

  .contact { position: absolute; left: 294px; top: 128px; list-style: none; font-size: 12.5px; line-height: 1.15; }
  .contact li { display: flex; align-items: flex-start; margin-bottom: 12px; }
  .contact svg { width: 14px; height: 16px; flex: none; margin-right: 12px; }
  .card--back-light .contact { color: var(--text-grey); }
  .card--back-dark .contact { color: var(--paper); }
</style>
</head>
<body>

  <section class="card card--front-top">
    <div class="skyline" role="img" aria-label="Faint city skyline silhouette"></div>
    <div class="brand">
      <span class="brand__mark"></span>
      <span class="brand__name">Summit Builders</span>
      <span class="brand__license">CSLB License # 2418596</span>
    </div>
  </section>

  <section class="card card--front-bottom">
    <div class="brand">
      <span class="brand__mark"></span>
      <span class="brand__name">Summit Builders</span>
      <span class="brand__license">CSLB License # 2418596</span>
    </div>
  </section>

  <section class="card card--back-light">
    <svg class="card__shape" viewBox="0 0 520 297" aria-hidden="true">
      <polygon points="0,0 267,0 225,148 267,297 0,297" fill="var(--orange)"/>
      <polygon points="267,0 271,0 235,148 271,297 267,297 225,148" fill="var(--charcoal)"/>
    </svg>
    <div class="skyline" role="img" aria-label="Faint city skyline silhouette"></div>
    <div class="brand">
      <span class="brand__mark"></span>
      <span class="brand__name">Summit Builders</span>
      <span class="brand__license">CSLB License # 2418596</span>
    </div>
    <div class="person">
      <p class="person__name">JORDAN REYES</p>
      <p class="person__title">DIRECTOR</p>
    </div>
    <ul class="contact">
      <li><svg viewBox="0 0 14 16"><path d="M7 0a6 6 0 0 0-6 6c0 4.5 6 10 6 10s6-5.5 6-10a6 6 0 0 0-6-6zm0 8.5a2.5 2.5 0 1 1 0-5 2.5 2.5 0 0 1 0 5z" fill="var(--orange)"/></svg><span>245 Maple Grove Ave #B2<br>Austin 78701 TX</span></li>
      <li><svg viewBox="0 0 14 16"><rect x="0" y="4" width="14" height="9" fill="var(--orange)"/><path d="M0 4l7 5 7-5" stroke="#fff" stroke-width="1.2" fill="none"/></svg><span>info@summitbuildersca.example</span></li>
      <li><svg viewBox="0 0 14 16"><path d="M3 2l2.5 3-1.5 1.5a8 8 0 0 0 4.5 4.5L10 9.5l3 2.5-1.5 2.5C6 14 1 9 1.5 3.5z" fill="var(--orange)"/></svg><span>(512) 555 0148</span></li>
      <li><svg viewBox="0 0 14 16"><rect x="2.5" y="0.5" width="9" height="15" rx="1.5" fill="none" stroke="var(--orange)" stroke-width="1.6"/><rect x="5.5" y="12.5" width="3" height="1.2" fill="var(--orange)"/></svg><span>(512) 555 0172</span></li>
    </ul>
  </section>

  <section class="card card--back-dark">
    <svg class="card__shape" viewBox="0 0 520 297" aria-hidden="true">
      <polygon points="0,0 267,0 225,148 267,297 0,297" fill="var(--orange)"/>
      <polygon points="267,0 271,0 235,148 271,297 267,297 225,148" fill="var(--paper)"/>
    </svg>
    <div class="skyline" role="img" aria-label="Faint city skyline silhouette"></div>
    <div class="brand">
      <span class="brand__mark"></span>
      <span class="brand__name">Summit Builders</span>
      <span class="brand__license">CSLB License # 2418596</span>
    </div>
    <div class="person">
      <p class="person__name">JORDAN REYES</p>
      <p class="person__title">DIRECTOR</p>
    </div>
    <ul class="contact">
      <li><svg viewBox="0 0 14 16"><path d="M7 0a6 6 0 0 0-6 6c0 4.5 6 10 6 10s6-5.5 6-10a6 6 0 0 0-6-6zm0 8.5a2.5 2.5 0 1 1 0-5 2.5 2.5 0 0 1 0 5z" fill="var(--orange)"/></svg><span>418 W Orchard Ave Suite 5<br>Fullerton, CA 92832</span></li>
      <li><svg viewBox="0 0 14 16"><rect x="0" y="4" width="14" height="9" fill="var(--orange)"/><path d="M0 4l7 5 7-5" stroke="var(--charcoal)" stroke-width="1.2" fill="none"/></svg><span>info@summitbuildersca.example</span></li>
      <li><svg viewBox="0 0 14 16"><path d="M3 2l2.5 3-1.5 1.5a8 8 0 0 0 4.5 4.5L10 9.5l3 2.5-1.5 2.5C6 14 1 9 1.5 3.5z" fill="var(--orange)"/></svg><span>714-555-0133</span></li>
      <li><svg viewBox="0 0 14 16"><rect x="2.5" y="0.5" width="9" height="15" rx="1.5" fill="none" stroke="var(--orange)" stroke-width="1.6"/><rect x="5.5" y="12.5" width="3" height="1.2" fill="var(--orange)"/></svg><span>714-555-0186</span></li>
    </ul>
  </section>

</body>
</html>
```